cleaning service

we are a cleaning company,

we have a current flyer but its very dull

I have attached it, can we make it look modern, maybe add pictures and colour

```html
<!DOCTYPE html>
<html lang="en">
<head>
<meta charset="utf-8">
<title>Brightway Cleaning Services – Tri-fold Brochure</title>
<link href="https://fonts.googleapis.com/css2?family=Arimo:wght@400;700&family=Montserrat:wght@500;600;700&display=swap" rel="stylesheet">
<style>
:root{
  --bg:#ebebeb;
  --maroon:#6f0d33;
  --maroon-light:#a4164f;
  --gold:#c59a2d;
  --gold-light:#e2c261;
  --cream:#f8f0da;
  --red:#c5161d;
  --ink:#3a3a3a;
  --white:#ffffff;
}
*{margin:0;padding:0;box-sizing:border-box}
html,body{width:829px;height:1200px;overflow:hidden;background:var(--bg)}
body{position:relative;font-family:"Arimo",Arial,sans-serif;color:var(--ink)}
.sheet{position:absolute;left:67px;width:696px;height:492px;display:flex;box-shadow:0 6px 14px rgba(0,0,0,.25);background:var(--white)}
.sheet--outside{top:62px}
.sheet--inside{top:618px}
.panel{position:relative;width:232px;height:492px;overflow:hidden}
.panel > *{position:absolute}
.panel--white{background:var(--white)}
.panel--maroon{background:radial-gradient(ellipse at 50% 40%,var(--maroon-light),var(--maroon) 75%)}
.gold-block{background:linear-gradient(160deg,#b98b22,#d4ad45 50%,#b98b22)}
.photo{left:0;width:232px}
.icon{width:20px;height:24px;border-radius:3px;background:var(--red)}
.heading{font-size:9px;color:var(--red);font-weight:400}
.maroon-text .heading{color:var(--gold-light)}
.copy{font-size:6px;line-height:7.3px;text-align:justify;left:14px;width:204px}
.maroon-text .copy{color:var(--white)}
.fine{font-size:4.6px;line-height:5.3px;text-align:justify;left:14px;width:204px;color:var(--red)}
.maroon-text .fine{color:#ffb2b2}
.price-table{left:14px;width:204px;background:var(--cream);border-radius:3px;padding:0 0 4px;font-size:5.4px}
.price-table .bar{background:var(--gold);color:var(--white);text-align:center;font-size:6px;line-height:9px;margin-bottom:4px;letter-spacing:.2px}
.price-table table{border-collapse:collapse;margin-left:10px}
.price-table td{padding:0;line-height:6.6px}
.price-table td:first-child{width:112px}
.pill{left:14px;width:204px;height:13px;border:1px solid #d6c79a;border-radius:7px;background:var(--white);font-size:6.2px;line-height:11px;padding-left:10px;color:#333}
.pill em{font-style:normal;color:var(--red);margin-left:8px}
.about-title{font-family:"Montserrat",sans-serif;font-weight:600;font-size:13px;color:var(--white);left:14px;top:28px;letter-spacing:.5px}
.about-copy{color:var(--white);font-size:7px;line-height:8.6px;left:14px;width:204px;text-align:justify}
.brand-title{font-family:"Montserrat",sans-serif;font-weight:500;color:var(--white);text-align:center;width:232px;left:0;letter-spacing:.6px}
.brand-sub{font-family:"Montserrat",sans-serif;font-weight:500;color:var(--white);text-align:center;width:232px;left:0;letter-spacing:1px}
.offer-copy{color:var(--white);font-size:8.2px;line-height:14px;text-align:center;width:212px;left:10px}
.call-bar{left:12px;width:206px;height:18px;border-radius:9px;background:linear-gradient(90deg,#c79c2f,#ecd27a 50%,#c79c2f);font-weight:700;font-size:8.6px;line-height:18px;text-align:center;color:#2b0a16}
.call-bar svg{vertical-align:-1px;margin:0 3px 0 5px}
.tagline{left:0;width:232px;text-align:center;color:var(--white);font-weight:700;font-size:8.4px}
.call-line{left:0;width:232px;text-align:center;font-weight:700;font-size:8px;color:#222}
.badge{width:66px;height:66px;border-radius:50%;background:radial-gradient(circle,#d0202c,#9c0f1c);border:2px solid var(--gold-light);color:var(--white);text-align:center;font-family:"Montserrat",sans-serif;font-weight:700;font-size:22px;padding-top:8px}
.badge small{font-size:7px}
.ribbon{height:16px;background:#b3121e;color:var(--white);font-family:"Montserrat",sans-serif;font-weight:700;font-size:9.5px;line-height:16px;text-align:center;letter-spacing:.3px;border-top:1px solid var(--gold-light);border-bottom:1px solid var(--gold-light)}
.circle-photo{border-radius:50%;border:3px solid var(--white)}
.swoosh{left:0;width:232px}
</style>
</head>
<body>

<section class="sheet sheet--outside">

  <div class="panel panel--white">
    <div class="icon" role="img" aria-label="Curtain cleaning icon" style="left:12px;top:16px"></div>
    <h3 class="heading" style="left:52px;top:34px">Curtain Cleaning</h3>
    <p class="copy" style="top:52px">The cleaning specialists will use professional equipment and will wipe all washable surfaces down in order to eradicate and disinfect from all the harmful germs. Our broad spectrum and certified disinfectant is perfect for disease control or precautionary measure in any property or business, in order to ensure and maintain hygienic conditions. Our antiviral sanitisation service can be requested separately or combined with any of our other services.</p>
    <div class="price-table" style="top:118px">
      <div class="bar">CURTAIN CLEANING</div>
      <table><tr><td>Pair of curtains – half length</td><td>£24</td></tr><tr><td>Pair of curtains – full length</td><td>£29</td></tr></table>
    </div>
    <div class="icon" role="img" aria-label="Window cleaning icon" style="left:12px;top:166px"></div>
    <h3 class="heading" style="left:52px;top:185px">Window Cleaning</h3>
    <p class="copy" style="top:203px">Brightway Cleaning services offers professional window cleaning services in London. Our well-trained and vetted cleaners will do a fantastic job in keeping your property's windows bright and clean, ensuring that windows, frames and sills are cleaned professionally. You can benefit from our great expertise and affordable prices for London window cleaning.</p>
    <div class="photo" role="img" aria-label="Bright dining room with white table and chairs" style="top:290px;height:202px;background:linear-gradient(160deg,#e9e4dc,#c9bba6 55%,#8f7c68)"></div>
    <svg class="swoosh" style="top:268px" width="232" height="40" viewBox="0 0 232 40" aria-hidden="true">
      <path d="M0 0H232V8C150 8 70 18 0 38Z" fill="#fff"/>
      <path d="M0 30C70 12 150 6 232 8V13C150 12 70 20 0 38Z" fill="#c59a2d"/>
    </svg>
  </div>

  <div class="panel panel--maroon maroon-text">
    <div class="gold-block" style="left:0;top:0;width:232px;height:345px"></div>
    <h2 class="about-title">ABOUT US</h2>
    <p class="about-copy" style="top:48px">Brightway Cleaning Services offers professional cleaning services to make your home look its very best. From cleaning sinks, baths and tiles to polishing windows, our cleaners have the expertise to deal with every cleaning challenge.</p>
    <p class="about-copy" style="top:96px">Let me customise a cleaning service programme to suit your individual needs and your budget. Whether you require a regular service (daily, weekly or monthly) or just a one-off service, you can count on Brightway Cleaning services for a cleaning service at excellent rates.</p>
    <p class="about-copy" style="top:158px">In addition, Brightway Cleaning Services believes that the products we use really matter. All the products we use are natural and non-toxic, which makes them healthier for your home and safer for the local London environment. I have personally research all our house cleaning products to ensure they are non-toxic, biodegradable and not tested on animals.</p>
    <svg class="swoosh" style="top:318px" width="232" height="50" viewBox="0 0 232 50" aria-hidden="true">
      <path d="M0 20C80 50 150 0 232 30V50H0Z" fill="#7a1038"/>
      <path d="M0 16C80 44 150 -4 232 24V30C150 2 80 50 0 22Z" fill="#fff"/>
      <path d="M0 22C80 50 150 2 232 30V33C150 6 80 52 0 25Z" fill="#e2c261"/>
    </svg>
    <div class="circle-photo" role="img" aria-label="Vacuum cleaner on a carpet" style="left:70px;top:248px;width:96px;height:96px;background:radial-gradient(circle at 45% 40%,#d9d9dc,#8a8c93 60%,#4e4f55)"></div>
    <h2 class="brand-title" style="top:354px;font-size:13.5px">CLEANING SERVICES</h2>
    <p class="brand-sub" style="top:374px;font-size:10px">BY BRIGHTWAY GAZETTE</p>
    <p class="offer-copy" style="top:406px">We can integrate the cleaning services with the newspaper delivery services and as well are offering a 20% off for all our newspaper customers and £50 for introducing us to your family and friends.</p>
  </div>

  <div class="panel panel--maroon">
    <div class="photo" role="img" aria-label="Smiling family sitting together in a bright living room" style="top:0;height:370px;background:linear-gradient(170deg,#efe9e2,#d6c3ad 45%,#9c8a78)"></div>
    <svg class="swoosh" style="top:320px" width="232" height="60" viewBox="0 0 232 60" aria-hidden="true">
      <path d="M0 60V40C80 20 160 14 232 24V60Z" fill="#7a1038"/>
      <path d="M0 34C80 14 160 8 232 18V24C160 14 80 20 0 40Z" fill="#c59a2d"/>
      <path d="M0 40C80 20 160 14 232 24V27C160 18 80 24 0 44Z" fill="#fff"/>
    </svg>
    <div class="badge" style="left:132px;top:268px">20%<small>OFF</small></div>
    <div class="ribbon" style="left:112px;top:320px;width:116px">SPECIAL OFFER</div>
    <h2 class="brand-title" style="top:383px;font-size:17px">CLEANING SERVICES</h2>
    <p class="brand-sub" style="top:410px;font-size:12px">BY BRIGHTWAY GAZETTE</p>
    <div class="call-bar" style="top:446px">PLEASE CALL US ON<svg width="8" height="8" viewBox="0 0 24 24"><path d="M6.6 10.8a15 15 0 0 0 6.6 6.6l2.2-2.2a1 1 0 0 1 1-.25 11 11 0 0 0 3.6.6 1 1 0 0 1 1 1V20a1 1 0 0 1-1 1A17 17 0 0 1 3 4a1 1 0 0 1 1-1h3.5a1 1 0 0 1 1 1 11 11 0 0 0 .6 3.6 1 1 0 0 1-.25 1Z" fill="#2b0a16"/></svg>07700 900123</div>
    <p class="tagline" style="top:470px">TO BEAT ANY PRICE</p>
  </div>
</section>

<section class="sheet sheet--inside">

  <div class="panel panel--white">
    <div class="photo" role="img" aria-label="Bright living room with white sofas" style="top:0;height:196px;background:linear-gradient(160deg,#f1efec,#cfc8c0 50%,#7c8087)"></div>
    <svg class="swoosh" style="top:160px" width="232" height="50" viewBox="0 0 232 50" aria-hidden="true">
      <path d="M0 50V28C80 30 160 20 232 6V50Z" fill="#fff"/>
      <path d="M0 20C80 24 160 14 232 0V6C160 20 80 30 0 28Z" fill="#c59a2d"/>
    </svg>
    <div class="icon" role="img" aria-label="Antiviral sanitisation icon" style="left:20px;top:204px;width:16px;height:18px"></div>
    <h3 class="heading" style="left:45px;top:212px">Antiviral Sanitisation Service</h3>
    <p class="copy" style="top:227px">The cleaning specialists will use professional equipment and will wipe all washable surfaces down in order to eradicate and disinfect from all the harmful germs. Our broad spectrum and certified disinfectant is perfect for disease control or precautionary measure in any property or business, in order to ensure and maintain hygienic conditions. Our antiviral sanitisation service can be requested separately or combined with any of our other services.</p>
    <p class="fine" style="top:293px">BS EN 1276 is the European standard for the bactericidal activity of chemical disinfectants. To prove effective infection control against harmful micro-organisms such as MRSA, salmonella, E.coli and influenza A, products must be tested by an independent laboratory and prove a bacterium kill rate of 99.999% within five minutes.</p>
    <div class="pill" style="top:330px">Including our cleaning materials <em>£16 (per hour)</em></div>
    <div class="icon" role="img" aria-label="Deep cleaning icon" style="left:14px;top:360px;width:18px;height:22px"></div>
    <h3 class="heading" style="left:45px;top:368px">One Off Deep Cleaning Service</h3>
    <p class="copy" style="top:383px">If you require one-off cleaning to freshen up your home Brightway Cleaning Services can help you. We can arrange for a team of professional cleaners to come to your home at a time that's convenient for you. Our deep cleaning service is perfect for all households looking to save themselves from tiresome home spring cleaning.</p>
    <p class="fine" style="top:427px">Our one-off service is a deep cleaning of your home, rental or holiday house in London and the nearby towns. Our team can bring cleaning solutions and equipment, or we can use the tools and supplies you provide. We will work according to your requirements and can create a checklist with the areas you want us to clean. The service is perfect for your spring cleaning or any other general clean-up of the house.</p>
    <div class="pill" style="top:464px">Including our cleaning materials <em>£16 (per hour)</em></div>
  </div>

  <div class="panel panel--maroon maroon-text">
    <div class="icon" role="img" aria-label="Carpet cleaning icon" style="left:14px;top:20px;width:22px;height:20px;background:var(--gold-light)"></div>
    <h3 class="heading" style="left:45px;top:25px">Carpet Cleaning</h3>
    <p class="copy" style="top:40px">Brightway Cleaning services provides professional carpet cleaning service, carried out by our certified cleaners with years of professional experience. Our reputation speaks for itself.</p>
    <p class="fine" style="top:66px">We provide a high-quality deep carpet cleaning service for all types of rugs and carpets. The method we apply when tending to textile floorings is hot water extraction, also known as steam cleaning. We also do stain removal, treating even old stubborn spots and spills on all types of rugs. With us, you can also add fabric stain protection to enhance the results of the deep carpet cleaning.</p>
    <div class="price-table" style="top:101px;background:#fff">
      <div class="bar">CARPET CLEANING</div>
      <table>
        <tr><td>Single Bedroom</td><td>£19</td></tr>
        <tr><td>Double Bedroom</td><td>£24</td></tr>
        <tr><td>Living / Dining / Lounge</td><td>£29</td></tr>
        <tr><td>Hallway</td><td>£13</td></tr>
        <tr><td>Landing</td><td>£7</td></tr>
        <tr><td>Steps</td><td>£2 ( per step )</td></tr>
        <tr><td>Bathroom</td><td>£6</td></tr>
      </table>
    </div>
    <div class="pill" style="top:180px">Including our cleaning materials <em>Minimum charge of £49</em></div>
    <div class="circle-photo" role="img" aria-label="Gloved hand cleaning a window" style="left:26px;top:210px;width:66px;height:66px;background:radial-gradient(circle,#cfe3f2,#5f8fbf)"></div>
    <div class="circle-photo" role="img" aria-label="Carpet being steam cleaned" style="left:83px;top:210px;width:66px;height:66px;background:radial-gradient(circle,#e6e0d6,#9c9186)"></div>
    <div class="circle-photo" role="img" aria-label="Gloved hand wiping a kitchen surface" style="left:142px;top:210px;width:66px;height:66px;background:radial-gradient(circle,#f3e6a5,#b59a3d)"></div>
    <div class="icon" role="img" aria-label="Rug cleaning icon" style="left:14px;top:284px;width:20px;height:20px;background:var(--gold-light)"></div>
    <h3 class="heading" style="left:45px;top:293px">Rug Cleaning</h3>
    <p class="copy" style="top:309px">Brightway Cleaning services offers professional rug cleaning service at competitive prices! Book our skilled technicians and have your textile floorings impeccably cleaned in no time. We will bring the as-new look of any rug, including antique rugs, Persian rugs, area rugs and more. If you need us to deal with a nasty stain or any other accident on your rug, you can now book our emergency rug cleaning service for a same-day appointment at no extra cost!</p>
    <div class="icon" role="img" aria-label="Oven cleaning icon" style="left:14px;top:378px;width:20px;height:20px;background:var(--gold-light)"></div>
    <h3 class="heading" style="left:45px;top:388px">Oven Cleaning <span style="color:#fff">From £42</span></h3>
    <p class="copy" style="top:404px">Brightway Cleaning services offers professional rug cleaning service at competitive prices! Book our skilled technicians and have your textile floorings impeccably cleaned in no time. We will bring the as-new look of any rug, including antique rugs, Persian rugs, area rugs and more. If you need us to deal with a nasty stain or any other accident on your rug, you can now book our emergency rug cleaning service for a same-day appointment at no extra cost!</p>
    <p class="fine" style="top:458px">Brightway Cleaning services provides professional oven cleaning in all London boroughs. You can hire us to clean the stove in your home or restaurant. We will remove the grease and burnt food from hob or gas burners, and clean the appliance inside and out, including the door and the racks.</p>
  </div>

  <div class="panel panel--white">
    <div class="icon" role="img" aria-label="Upholstery cleaning icon" style="left:14px;top:20px;width:22px;height:18px"></div>
    <h3 class="heading" style="left:45px;top:26px">Upholstery Cleaning</h3>
    <p class="copy" style="top:40px">Keeping your home clean is vital and taking care of upholstery is an important part of that. If you're struggling to find time around the demands of family and/or career, Brightway Cleaning services can help.</p>
    <div class="price-table" style="top:69px">
      <div class="bar">UPHOLSTERY CLEANING</div>
      <table>
        <tr><td>Armchair</td><td>£17</td></tr>
        <tr><td>Two seater sofa</td><td>£22</td></tr>
        <tr><td>Three seater sofa</td><td>£32</td></tr>
        <tr><td>Four seater sofa</td><td>£42</td></tr>
        <tr><td>Dining chair</td><td>£6</td></tr>
      </table>
    </div>
    <p class="fine" style="top:131px">Our upholstery cleaning team is focused on delivering an outstanding result when treating your sofa or armchairs. We can also clean loveseats, dining chairs, ottomans and other types of furnishings. We clean various upholstery types, including natural materials like leather, wool and suede, as well as fibre blends and microfiber.</p>
    <div class="pill" style="top:164px">Including our cleaning materials <em>Minimum charge of £49</em></div>
    <div class="icon" role="img" aria-label="Mattress cleaning icon" style="left:14px;top:192px;width:24px;height:16px"></div>
    <h3 class="heading" style="left:45px;top:195px">Mattress Cleaning</h3>
    <p class="copy" style="top:210px">Brightway Cleaning Services provides mattress cleaning for your residential property in. Our technicians use safe but efficient solutions and powerful professional equipment to remove dirt, dust, and bacteria from your bedding. We can deal with all kinds of stains on your mattress and will restore its as-new look at an inexpensive price.</p>
    <div class="price-table" style="top:254px">
      <div class="bar">MATTRESS CLEANING</div>
      <table>
        <tr><td>Single Mattress both sides</td><td>£19</td></tr>
        <tr><td>Double Mattress both sides</td><td>£29</td></tr>
      </table>
    </div>
    <p class="call-line" style="top:300px">PLEASE CALL US ON &nbsp;<svg width="8" height="8" viewBox="0 0 24 24" style="vertical-align:-1px"><path d="M6.6 10.8a15 15 0 0 0 6.6 6.6l2.2-2.2a1 1 0 0 1 1-.25 11 11 0 0 0 3.6.6 1 1 0 0 1 1 1V20a1 1 0 0 1-1 1A17 17 0 0 1 3 4a1 1 0 0 1 1-1h3.5a1 1 0 0 1 1 1 11 11 0 0 0 .6 3.6 1 1 0 0 1-.25 1Z" fill="#222"/></svg> 07700 900123</p>
    <div class="photo" role="img" aria-label="Calm white bedroom with a made bed" style="top:340px;height:152px;background:linear-gradient(160deg,#eeeae4,#cbc3b8 55%,#8d8378)"></div>
    <svg class="swoosh" style="top:312px" width="232" height="70" viewBox="0 0 232 70" aria-hidden="true">
      <path d="M0 0H232V10C160 40 80 58 0 54Z" fill="#fff"/>
      <path d="M0 54C80 58 160 40 232 10V20C160 50 80 66 0 62Z" fill="#c59a2d"/>
      <path d="M0 62C80 66 160 50 232 20V24C160 54 80 70 0 66Z" fill="#e2c261"/>
    </svg>
  </div>
</section>

</body>
</html>
```